Verodex business card

Business card for sustainable investment company called "Verodex". Verodex is an exchange platform selling carbon credits between buyers and sellers. Carbon Credits are an environmental commodity for reducing global carbon emissions.

the card should obviously have our logo and the theme should be sustainability/environment mixed with a trading platform.

Contact Information for Business Card

Logo, Name, Title, Phone, Email

Colors
0054AA
0677BA
7BADD7
CADEEF
E8F1F8
0094D4
00A9DD
6FCCEA
C7EBF8
E9F6FB
00AB8E
00BBA5
67D7C9
C6EFE9
E9F9F6
59FF00
82FF00
B8FF75
E3FFCB
F4FFEA

```html
<!DOCTYPE html>
<html lang="en">
<head>
<meta charset="utf-8">
<title>Verodex Business Card</title>
<link rel="stylesheet" href="https://fonts.googleapis.com/css2?family=Montserrat:wght@500;600;700&family=Roboto+Slab:wght@300;400&display=swap">
<style>
  :root {
    --stage: #2b2b2d;
    --navy: #15284f;
    --navy-deep: #112246;
    --sky: #30aee3;
    --white: #ffffff;
    --paper: #f7f8f9;
    --pattern: #eceef0;
    --rule-grey: #d9dadc;
  }
  * { margin: 0; padding: 0; box-sizing: border-box; }
  html, body { width: 1200px; height: 960px; overflow: hidden; }
  body { background: var(--stage); position: relative; font-family: "Montserrat", sans-serif; }

  .card {
    position: absolute;
    left: 250px;
    width: 700px;
    height: 400px;
    border-radius: 22px;
    overflow: hidden;
    box-shadow: 0 14px 30px rgba(0,0,0,.45);
  }
  .card--back { top: 60px; background: linear-gradient(135deg, #1d3563 0%, var(--navy) 45%, var(--navy-deep) 100%); }
  .card--front { top: 500px; background: var(--navy); }

  .wordmark {
    position: absolute;
    display: flex;
    align-items: center;
    gap: 16px;
    font-weight: 600;
    letter-spacing: 2px;
    text-transform: uppercase;
    white-space: nowrap;
  }
  .wordmark__dot { border-radius: 50%; background: var(--sky); flex: none; }
  .card--back .wordmark { left: 50%; top: 50%; transform: translate(-50%, -50%); font-size: 64px; color: var(--white); }
  .card--back .wordmark__dot { width: 58px; height: 58px; }
  .card--front .wordmark { left: 440px; top: 172px; font-size: 34px; color: var(--navy); }
  .card--front .wordmark__dot { width: 34px; height: 34px; }

  .front-shapes { position: absolute; inset: 0; }

  .holder { position: absolute; left: 100px; top: 60px; color: var(--white); white-space: nowrap; }
  .holder__name { font-size: 25px; font-weight: 700; letter-spacing: 1px; }
  .holder__title { font-size: 18px; font-weight: 500; margin-top: 2px; letter-spacing: .5px; }

  .contact { position: absolute; font-family: "Roboto Slab", serif; font-weight: 300; color: var(--white); font-size: 15px; line-height: 1.3; white-space: nowrap; }
  .contact--phone { left: 128px; top: 142px; }
  .contact--web { left: 158px; top: 212px; }
  .contact--address { left: 188px; top: 282px; }
</style>
</head>
<body>

  <section class="card card--back" aria-label="Card back">
    <div class="wordmark"><span class="wordmark__dot"></span>Verodex</div>
  </section>

  <section class="card card--front" aria-label="Card front">
    <svg class="front-shapes" width="700" height="400" viewBox="0 0 700 400">
      <clipPath id="panelClip"><polygon points="392,0 700,0 700,400 590,400 392,292"/></clipPath>
      <polygon class="panel-white" points="392,0 700,0 700,400 590,400 392,292" fill="var(--paper)"/>
      <rect x="392" y="0" width="308" height="400" fill="var(--pattern)" opacity=".35" role="img" aria-label="Faint triangle pattern" clip-path="url(#panelClip)"/>
      <polyline class="rule-grey" points="374,140 374,300 540,392" fill="none" stroke="var(--rule-grey)" stroke-width="9"/>
      <polygon class="tri-top" points="272,0 366,0 366,96" fill="var(--sky)"/>
      <line x1="380" y1="0" x2="380" y2="108" stroke="var(--white)" stroke-width="6"/>
      <polygon class="tri-bottom" points="545,400 650,400 545,346" fill="var(--sky)"/>
      <line x1="545" y1="340" x2="664" y2="400" stroke="var(--white)" stroke-width="6"/>

      <g class="icon-chain" fill="none" stroke="var(--sky)" stroke-width="3">
        <polyline points="70,90 100,160 130,230 160,300"/>
        <polygon points="56,90 63,77 77,77 84,90 77,103 63,103" fill="var(--sky)"/>
        <polygon points="86,160 93,147 107,147 114,160 107,173 93,173" fill="var(--navy)"/>
        <polygon points="116,230 123,217 137,217 144,230 137,243 123,243" fill="var(--navy)"/>
        <polygon points="146,300 153,287 167,287 174,300 167,313 153,313" fill="var(--navy)"/>
      </g>
      <g class="icons" fill="var(--white)">
        <circle cx="70" cy="86" r="4"/>
        <path d="M62 97 q8 -9 16 0 z"/>
        <path d="M93 163 h14 l-2 -6 h-10 z M94 156 q6 -5 12 0" stroke="var(--white)" stroke-width="1.5"/>
        <g fill="none" stroke="var(--white)" stroke-width="1.4">
          <circle cx="130" cy="230" r="7"/>
          <ellipse cx="130" cy="230" rx="3" ry="7"/>
          <line x1="123" y1="230" x2="137" y2="230"/>
        </g>
        <path d="M160 308 l-6 -9 a6 6 0 1 1 12 0 z"/>
        <circle cx="160" cy="297" r="2" fill="var(--navy)"/>
      </g>
    </svg>

    <div class="holder">
      <div class="holder__name">MARCUS HALE</div>
      <div class="holder__title">Founder</div>
    </div>
    <div class="contact contact--phone">000 555 0142<br>000 555 0143</div>
    <div class="contact contact--web">hello@verodex.com<br>www.verodex.com</div>
    <div class="contact contact--address">212, 3rd Floor,<br>Elm Road, NY 104455</div>

    <div class="wordmark"><span class="wordmark__dot"></span>Verodex</div>
  </section>

</body>
</html>
```